Business card for medical clinic

I need an upmarket, modern medical/health business card for my clinic

Contact Information for Business Card

name, address, email, qr code

```html
<!DOCTYPE html>
<html lang="en">
<head>
<meta charset="utf-8">
<title>Corvane Health Partners – Business Card</title>
<link rel="stylesheet" href="https://fonts.googleapis.com/css2?family=Montserrat:wght@400;500;700&display=swap">
<style>
  :root {
    --backdrop: #2a2a2c;
    --card: #ffffff;
    --navy: #1b5f8f;
    --sky: #25a9e3;
    --ink: #1d1d1f;
  }
  * { box-sizing: border-box; margin: 0; padding: 0; }
  html, body { width: 1200px; height: 880px; overflow: hidden; }
  body {
    background: var(--backdrop);
    font-family: "Montserrat", Arial, sans-serif;
    position: relative;
  }
  .card {
    position: absolute;
    left: 240px;
    width: 720px;
    height: 411px;
    background: var(--card);
    border-radius: 24px;
    overflow: hidden;
  }
  .card--front { top: 22px; }
  .card--back { top: 447px; }

  .brand {
    position: absolute;
    display: flex;
    align-items: center;
    color: var(--navy);
    font-weight: 700;
    text-transform: uppercase;
    white-space: nowrap;
  }
  .brand__dot {
    border-radius: 50%;
    border: 6px solid var(--navy);
    margin-right: 18px;
    flex: none;
  }
  .card--front .brand {
    left: 0;
    right: 0;
    top: 160px;
    justify-content: center;
    font-size: 27px;
    letter-spacing: 1px;
  }
  .card--front .brand__dot { width: 90px; height: 90px; }
  .card--back .brand { left: 44px; top: 175px; font-size: 17px; letter-spacing: 1px; }
  .card--back .brand__dot { width: 52px; height: 52px; border-width: 4px; margin-right: 10px; }

  .divider {
    position: absolute;
    left: 376px;
    top: 80px;
    width: 2px;
    height: 220px;
    background: var(--sky);
  }
  .contact {
    position: absolute;
    left: 402px;
    top: 74px;
    color: var(--ink);
  }
  .contact__name {
    color: var(--sky);
    font-weight: 700;
    font-size: 30px;
    letter-spacing: 0.5px;
    line-height: 1.05;
  }
  .contact__role { font-size: 16px; margin-top: 2px; }
  .contact__list { list-style: none; margin-top: 18px; font-size: 16px; }
  .contact__list li { display: flex; align-items: center; gap: 10px; line-height: 26px; }
  .contact__list svg { width: 16px; height: 16px; flex: none; }
  .contact__address { font-size: 16px; margin-top: 14px; line-height: 1.3; padding-left: 26px; }

  .footer-band { position: absolute; left: 0; bottom: 0; width: 720px; height: 110px; }
  .website {
    position: absolute;
    left: 300px;
    width: 262px;
    bottom: 26px;
    text-align: center;
    color: #ffffff;
    font-size: 17px;
    font-weight: 500;
    letter-spacing: 0.5px;
  }
</style>
</head>
<body>
  <section class="card card--front">
    <div class="brand"><span class="brand__dot"></span>Corvane Health Partners</div>
  </section>

  <section class="card card--back">
    <div class="brand"><span class="brand__dot"></span>Corvane Health</div>

    <div class="divider"></div>

    <div class="contact">
      <p class="contact__name">DANIEL MARSH</p>
      <p class="contact__role">Managing Director</p>
      <ul class="contact__list">
        <li>
          <svg viewBox="0 0 16 16" fill="var(--sky)"><path d="M3.5 1.5l2.5 2.5-1.5 2a9 9 0 0 0 5.5 5.5l2-1.5 2.5 2.5-2 2C6 14 2 10 1.5 3.5z"/></svg>
          123 456 789
        </li>
        <li>
          <svg viewBox="0 0 16 16" fill="none" stroke="var(--sky)" stroke-width="1.6"><rect x="4" y="1" width="8" height="14" rx="1.5"/><line x1="7" y1="12.5" x2="9" y2="12.5"/></svg>
          123 456 0000
        </li>
        <li>
          <svg viewBox="0 0 16 16" fill="none" stroke="var(--sky)" stroke-width="1.6"><rect x="1" y="3.5" width="14" height="9" rx="1"/><polyline points="1.5,4 8,9 14.5,4"/></svg>
          info@yourmail.com
        </li>
      </ul>
      <p class="contact__address">Your address, City<br>State, Zip 1234</p>
    </div>

    <svg class="footer-band" viewBox="0 0 720 110" aria-hidden="true">
      <line x1="28" y1="70" x2="290" y2="70" stroke="var(--sky)" stroke-width="2.5"/>
      <line x1="580" y1="32" x2="700" y2="32" stroke="var(--sky)" stroke-width="2.5"/>
      <polygon points="0,84 290,84 310,16 552,16 572,44 720,44 720,110 0,110" fill="var(--sky)"/>
    </svg>
    <p class="website">www.yourwebsite.com</p>
  </section>
</body>
</html>
```